Computer consultant business card

Bexil Software is a newly started computer consulting company. It's a small one-man company that provides mostly Vornix applications but also websites in collaboration with designers. I'm running this company on the side of full time university studies.

I want the final design to be clean and memorable. Be creative! :)

Some inspiration:
http://www.pixelmarta.com/design/48317
http://www.pixelmarta.com/design/2739164/business-card-design-by-frostlynk
http://www.pixelmarta.com/design/604281/business-card-design-by-koralind-vestrabanu

See attachment for my company logo.
Updates

I would like to thank everyone for submitting! I'll need a couple of days to review and ultimately select a design.

Target Market(s)

Non-technical entrepreneurs and small companies.

Industry/Entity Type

University

Requirements
Must have
• My company logo.
In any way, both colors from my logo.
First- and last name, e-mail and phone number.
Double-sided design.
Nice to have
• Something creative with the symbol in my logo

```html
<!DOCTYPE html>
<html lang="en">
<head>
<meta charset="utf-8">
<title>Bexil Software – Business Card</title>
<link rel="stylesheet" href="https://fonts.googleapis.com/css2?family=Jost:wght@400;500;600&family=Arimo:wght@400&display=swap">
<style>
  :root {
    --stage: #e9e6e1;
    --label: #1a1a1a;
    --card-white: #ffffff;
    --ink: #2f2d2e;
    --ink-soft: #4a4a4a;
    --brand-blue: #4472c0;
    --card-black: #050505;
    --dot-grey: #6e6a6c;
    --slate-top: #2e2f35;
    --slate-bottom: #48587e;
    --text-light: #ffffff;
  }
  * { box-sizing: border-box; margin: 0; padding: 0; }
  html, body {
    width: 1200px; height: 788px; overflow: hidden;
    background: var(--stage);
  }
  .sheet { position: relative; width: 1200px; height: 788px; }

  .side-label {
    position: absolute; width: 526px; text-align: center;
    font-family: "Arimo", Arial, sans-serif; font-size: 20px; color: var(--label);
  }

  .card {
    position: absolute; width: 526px; height: 300px;
    border-radius: 20px; overflow: hidden;
    box-shadow: 0 3px 8px rgba(0,0,0,.25);
    font-family: "Jost", "Helvetica Neue", sans-serif;
  }
  .card--front { left: 56px; top: 74px; background: var(--card-white); }
  .card--back-light { left: 622px; top: 74px; background: var(--card-white); }
  .card--back-dark { left: 53px; top: 445px; background: var(--card-black); }
  .card--back-slate {
    left: 622px; top: 445px;
    background: radial-gradient(ellipse at 55% 110%, var(--slate-bottom) 0%, #3b4460 45%, var(--slate-top) 100%);
  }

  .swoosh { position: absolute; inset: 0; width: 526px; height: 300px; }

  .brand { position: absolute; display: flex; align-items: center; }
  .brand__dot { border-radius: 50%; background: var(--brand-blue); flex: none; }
  .brand__name { font-weight: 500; line-height: 1; letter-spacing: 1px; }

  .brand--small { left: 33px; top: 30px; gap: 14px; }
  .brand--small .brand__dot { width: 44px; height: 44px; }
  .brand--small .brand__name { font-size: 56px; color: var(--ink); }

  .brand--large { left: 0; right: 0; top: 92px; justify-content: center; gap: 22px; }
  .brand--large .brand__dot { width: 78px; height: 78px; }
  .brand--large .brand__name { font-size: 96px; color: var(--ink); }
  .brand--on-dark .brand__name { color: var(--text-light); }

  .person { position: absolute; left: 36px; top: 158px; }
  .person__name { font-size: 17px; font-weight: 600; color: var(--brand-blue); }
  .person__role { font-size: 12.5px; color: var(--ink-soft); margin-top: 1px; }

  .contact { position: absolute; left: 34px; top: 228px; font-size: 14.5px; color: var(--ink); line-height: 21px; }
  .contact b { font-style: italic; font-weight: 600; }

  .web {
    position: absolute; left: 0; right: 0; bottom: 30px; text-align: center;
    font-size: 17px; letter-spacing: 3.2px; color: var(--ink);
  }
  .web--light { color: var(--text-light); }

  .texture {
    position: absolute; border-radius: 50%;
    background: radial-gradient(circle, rgba(110,106,108,.55) 0%, rgba(110,106,108,.15) 55%, rgba(0,0,0,0) 75%);
  }
  .texture--top { left: 20px; top: -110px; width: 300px; height: 220px; }
  .texture--bottom { left: 300px; top: 150px; width: 280px; height: 240px; }
</style>
</head>
<body>
<main class="sheet">

  <div class="side-label" style="left:56px; top:35px;">Front</div>
  <section class="card card--front">
    <svg class="swoosh" viewBox="0 0 526 300" aria-hidden="true">
      <path d="M414 0 Q 560 150 441 300 L526 300 L526 0 Z" fill="var(--brand-blue)"/>
      <path d="M448 0 Q 575 120 506 300 L516 300 Q 590 120 478 0 Z" fill="var(--card-white)"/>
    </svg>
    <div class="brand brand--small">
      <span class="brand__dot"></span>
      <span class="brand__name">bexil</span>
    </div>
    <div class="person">
      <p class="person__name">First Name Last Name</p>
      <p class="person__role">Designation</p>
    </div>
    <div class="contact">
      <p><b>p</b> : +12 345 6789</p>
      <p><b>e</b> : info@bexilsoft.com</p>
    </div>
  </section>

  <div class="side-label" style="left:622px; top:35px;">Back - 1</div>
  <section class="card card--back-light">
    <div class="brand brand--large">
      <span class="brand__dot"></span>
      <span class="brand__name">bexil</span>
    </div>
    <p class="web">www.bexilsoft.com</p>
  </section>

  <div class="side-label" style="left:53px; top:405px;">Back - 2</div>
  <section class="card card--back-dark">
    <div class="texture texture--top" role="img" aria-label="Perforated metal dot texture"></div>
    <div class="texture texture--bottom" role="img" aria-label="Perforated metal dot texture"></div>
    <div class="brand brand--large brand--on-dark">
      <span class="brand__dot"></span>
      <span class="brand__name">bexil</span>
    </div>
    <p class="web web--light">www.bexilsoft.com</p>
  </section>

  <div class="side-label" style="left:622px; top:405px;">Back - 3</div>
  <section class="card card--back-slate">
    <div class="brand brand--large brand--on-dark">
      <span class="brand__dot"></span>
      <span class="brand__name">bexil</span>
    </div>
    <p class="web web--light">www.bexilsoft.com</p>
  </section>

</main>
</body>
</html>
```